Travel Agency Website - Simple General

Need a 7 page simple design that is pretty repetitive. Need to be able to load quickly that is SEO optimized. Trying to give ideas on what they can do, be personal as we are local, but at the same time come across as professional and get information easily with little burden.

- Landing Page
- Brimwell Vacations Page
- Family Trips
- Road Trips from Texas
- Other Destinations
- About Us Page
- Contact Us Page

Target Market(s)

Families

Coding

Coded - Design and coding required

Number of Pages Required

5+ page

Colors

Designer to choose colors to be used in the design.

Requirements
Must have
• Like it to flow easily with our logo. Use that for colors, etc.

```html
<!DOCTYPE html>
<html lang="en">
<head>
<meta charset="utf-8">
<title>Wander Lane Travel – Website Pages</title>
<link rel="stylesheet" href="https://fonts.googleapis.com/css2?family=Lexend:wght@400;500;600&family=Figtree:wght@400;500;600;700&display=swap">
<style>
:root{
  --board:#5f5f5f;
  --teal:#1f5d69;
  --teal-2:#2a6f7a;
  --gold:#c89a4c;
  --cream:#f3f0e6;
  --beige:#efe6d3;
  --line:#cfd6d3;
  --ink:#2f3a3c;
  --muted:#5c6668;
  --white:#ffffff;
}
*{box-sizing:border-box;margin:0;padding:0}
html,body{width:1200px;height:1046px;overflow:hidden;background:var(--board)}
.board{position:absolute;left:0;top:0;width:2055px;height:1792px;transform:scale(.58394);transform-origin:0 0;font-family:"Figtree",sans-serif;color:var(--ink)}
.page{position:absolute;overflow:hidden;background:linear-gradient(180deg,#e8eeea 0%,#eef0ea 30%,var(--cream) 60%,#f4f1e8 100%)}
.page > *{position:absolute}
.topbar{top:0;left:272px;width:296px;height:22px;background:var(--teal);border-radius:0 0 8px 8px;color:var(--white);font-size:7.5px;display:flex;align-items:center;justify-content:space-around;padding:0 8px}
.tb-item{display:flex;align-items:center;gap:5px;white-space:nowrap}
.tb-ic{width:12px;height:12px;border-radius:50%;background:var(--white);display:flex;align-items:center;justify-content:center}
.logo{left:32px;top:24px;display:flex;align-items:center;gap:6px;text-decoration:none}
.logo-dot{width:10px;height:10px;border-radius:50%;background:var(--gold)}
.logo-name{font-family:"Lexend",sans-serif;font-weight:600;font-size:17px;line-height:1.05;color:var(--teal)}
.nav{top:34px;left:152px;height:20px;display:flex;align-items:center;gap:11px;font-size:7.5px;color:var(--ink)}
.nav a{color:inherit;text-decoration:none;white-space:nowrap;padding:3px 0}
.nav a.active{border-bottom:1px solid var(--gold)}
.nav .home{width:9px;height:9px}
.pill{display:inline-flex;align-items:center;gap:8px;background:var(--gold);color:var(--white)!important;border-radius:12px;padding:4px 4px 4px 14px!important;margin-left:2px;font-size:7px}
.arrow{width:13px;height:13px;border-radius:50%;background:rgba(255,255,255,.22);display:inline-flex;align-items:center;justify-content:center}
.foot{left:0;bottom:0;width:100%;height:33px;background:var(--white);display:flex;align-items:center;font-size:6.5px;color:var(--ink)}
.foot .copy{position:absolute;left:0;width:62%;text-align:center}
.foot .social{position:absolute;right:62px;display:flex;gap:4px}
.foot .social span{width:11px;height:11px;border-radius:50%;background:var(--teal)}
.eyebrow{left:0;width:100%;text-align:center;font-family:"Lexend",sans-serif;font-size:12px;color:var(--teal);letter-spacing:.3px}
.title{left:0;width:100%;text-align:center;font-family:"Lexend",sans-serif;font-weight:600;color:var(--teal);line-height:1.05}
.lead{left:0;width:100%;text-align:center;font-size:9.5px;line-height:1.4;color:var(--ink)}
.photo{border-radius:3px}
.card{border-radius:2px;overflow:hidden}
.card .cap{position:absolute;left:0;bottom:0;width:100%;padding:30px 4px 10px;text-align:center;font-family:"Lexend",sans-serif;font-weight:500;font-size:8.5px;line-height:1.15;color:var(--white);background:linear-gradient(180deg,rgba(31,93,105,0),rgba(31,93,105,.85))}
.card .cap.gold{background:linear-gradient(180deg,rgba(200,154,76,0),rgba(200,154,76,.9))}
.card .cap small{display:block;font-size:4.5px;font-weight:400}
.panel{background:rgba(255,255,255,.55);border:1px solid #dcdcd2;border-radius:3px}
.panel-title{left:0;width:100%;text-align:center;font-family:"Lexend",sans-serif;font-weight:500;font-size:14px;color:var(--teal)}
.lbl{font-size:7px;font-weight:500;color:var(--ink);white-space:nowrap}
.field{height:28px;background:var(--white);border:1px solid var(--line);border-radius:2px;font-size:7px;color:var(--muted);display:flex;align-items:center;justify-content:space-between;padding:0 10px}
.field .cal{display:flex;align-items:center;gap:5px}
.area{background:var(--white);border:1px solid var(--line);border-radius:2px;font-size:7px;color:var(--muted);padding:12px 13px}
.btn{height:26px;border-radius:13px;background:var(--gold);color:var(--white);font-weight:600;font-size:8.5px;display:flex;align-items:center;justify-content:center;gap:10px}
.tab{height:28px;display:flex;align-items:center;justify-content:center;font-family:"Lexend",sans-serif;font-weight:500;font-size:11px;letter-spacing:.3px}
.trips{border-collapse:collapse;font-size:6.5px;color:var(--ink)}
.trips th{background:var(--teal);color:var(--white);font-weight:500;height:21px;text-align:left;padding-left:26px}
.trips td{height:29px;padding-left:26px}
.trips tr:nth-child(even) td{background:#efeadc}
.trips tr:nth-child(odd) td{background:#faf8f2}
</style>
</head>
<body>
<main class="board">

<!-- ============ HOME ============ -->
<section class="page" style="left:82px;top:95px;width:606px;height:428px">
  <div class="topbar"><span class="tb-item"><i class="tb-ic"><svg width="7" height="5" viewBox="0 0 7 5"><rect x=".3" y=".3" width="6.4" height="4.4" fill="none" stroke="#1f5d69" stroke-width=".6"/><path d="M.3 .3 3.5 2.8 6.7 .3" fill="none" stroke="#1f5d69" stroke-width=".6"/></svg></i>hello@wanderlanetravel.com</span><span class="tb-item"><i class="tb-ic"><svg width="7" height="7" viewBox="0 0 10 10"><path d="M2 1l2 2-1 1.3c.6 1.3 1.5 2.2 2.8 2.8L7 6l2 2-1.2 1.4C4.5 9 1 5.5.6 2.2Z" fill="#1f5d69"/></svg></i>Phone Number (555) 010 2468</span></div>
  <a class="logo"><span class="logo-dot"></span><span class="logo-name">Wander<br>Lane</span></a>
  <nav class="nav" style="left:153px;top:34px"><svg class="home" viewBox="0 0 10 10"><path d="M5 1 1 5h1.3v4h2.2V6.5h1V9h2.2V5H9Z" fill="#c89a4c"/></svg><a>Brimwell Vacations</a><a>Family Trips</a><a>Texas Road Trips</a><a>Other Destinations</a><a style="margin-left:8px">About Us</a><a class="pill">Contact Us <span class="arrow"><svg width="6" height="6" viewBox="0 0 6 6"><path d="M1 5 5 1M2 1h3v3" stroke="#fff" stroke-width=".8" fill="none"/></svg></span></a></nav>
  <p class="eyebrow" style="top:86px;font-size:13.5px">WANDER LANE TRAVEL</p>
  <h1 class="title" style="top:108px;font-size:29px;left:-8px">PLAN YOUR PERFECT TRIP</h1>
  <div class="card" style="left:28px;top:163px;width:135px;height:187px"><div class="photo" role="img" aria-label="Fairytale castle under a blue sky" style="position:absolute;inset:0;background:linear-gradient(180deg,#4d8fd0,#8fb6d8 45%,#3e6a7a)"></div><p class="cap">BRIMWELL VACATIONS<br>LAND &amp; SEA</p></div>
  <div class="card" style="left:167px;top:163px;width:135px;height:187px"><div class="photo" role="img" aria-label="Family sitting by a mountain lake" style="position:absolute;inset:0;background:linear-gradient(180deg,#b9cfe0,#7f9fb6 40%,#6c7a6a 75%,#a58a5c)"></div><p class="cap gold">FAMILY TRIPS</p></div>
  <div class="card" style="left:309px;top:163px;width:135px;height:187px"><div class="photo" role="img" aria-label="Red canyon landscape in Texas" style="position:absolute;inset:0;background:linear-gradient(180deg,#5f9fd6,#a9c7dc 30%,#c2642f 60%,#7a6a3a)"></div><p class="cap">TEXAS ROAD TRIPS<small>(Partnership with Pine Ridge Van Rentals)</small></p></div>
  <div class="card" style="left:447px;top:163px;width:135px;height:187px"><div class="photo" role="img" aria-label="Colourful cliffside seaside village" style="position:absolute;inset:0;background:linear-gradient(180deg,#3f8fd0,#d98a5a 40%,#c9a26b 60%,#2f6f8a)"></div><p class="cap">OTHER DESTINATIONS</p></div>
  <footer class="foot"><span class="copy">© 2026 Wander Lane Travel. All Right Reserved</span><span class="social"><span></span><span></span></span></footer>
</section>

<!-- ============ ABOUT ============ -->
<section class="page" style="left:82px;top:560px;width:601px;height:504px">
  <div class="topbar" style="left:275px;width:280px"><span class="tb-item"><i class="tb-ic"><svg width="7" height="5" viewBox="0 0 7 5"><rect x=".3" y=".3" width="6.4" height="4.4" fill="none" stroke="#1f5d69" stroke-width=".6"/><path d="M.3 .3 3.5 2.8 6.7 .3" fill="none" stroke="#1f5d69" stroke-width=".6"/></svg></i>hello@wanderlanetravel.com</span><span class="tb-item"><i class="tb-ic"><svg width="7" height="7" viewBox="0 0 10 10"><path d="M2 1l2 2-1 1.3c.6 1.3 1.5 2.2 2.8 2.8L7 6l2 2-1.2 1.4C4.5 9 1 5.5.6 2.2Z" fill="#1f5d69"/></svg></i>Phone Number (555) 010 2468</span></div>
  <a class="logo" style="left:44px"><span class="logo-dot"></span><span class="logo-name">Wander<br>Lane</span></a>
  <nav class="nav" style="left:158px;top:32px"><svg class="home" viewBox="0 0 10 10"><path d="M5 1 1 5h1.3v4h2.2V6.5h1V9h2.2V5H9Z" fill="#c89a4c"/></svg><a>Brimwell Vacations</a><a>Family Trips</a><a>Texas Road Trips</a><a>Other Destinations</a><a class="active" style="margin-left:4px">About Us</a><a class="pill">Contact Us <span class="arrow"><svg width="6" height="6" viewBox="0 0 6 6"><path d="M1 5 5 1M2 1h3v3" stroke="#fff" stroke-width=".8" fill="none"/></svg></span></a></nav>
  <p class="eyebrow" style="top:82px;font-size:10px">WHO WE ARE</p>
  <h1 class="title" style="top:96px;font-size:24px">ABOUT WANDER LANE<br>TRAVEL</h1>
  <div role="img" aria-label="Couple on a tropical beach with limestone cliffs, and a couple relaxing on a boat" style="left:40px;top:168px;width:265px;height:262px;border-radius:46% 40% 44% 38%;background:linear-gradient(160deg,#9fc2d8 0%,#4f8a6a 35%,#e8dcc4 60%,#d9a27a 80%,#8a6a52 100%);border:4px solid #fff"></div>
  <p style="left:325px;top:180px;width:240px;font-size:10.5px;line-height:1.4;color:var(--teal);font-weight:500">Creating unforgettable travel experiences, one journey at a time.</p>
  <p style="left:325px;top:219px;width:245px;font-size:6.8px;line-height:1.75;color:var(--ink)">At Wander Lane Travel, we believe travel should be exciting, stress-free, and filled with unforgettable memories. Whether you're dreaming of a magical Brimwell vacation, planning a fun family getaway, or exploring scenic road trip destinations, we're here to help make every step of your journey simple and enjoyable.</p>
  <p style="left:325px;top:292px;width:245px;font-size:6.8px;line-height:1.75;color:var(--ink)">We specialize in personalized travel planning tailored to your unique needs, preferences, and budget. From destination recommendations and itinerary planning to travel tips and support, our goal is to help you create experiences that bring families closer and adventures to life.</p>
  <ul style="left:328px;top:356px;list-style:none;font-size:7px;line-height:2.05;color:var(--teal)">
    <li><svg width="8" height="6" viewBox="0 0 8 6"><path d="M1 3l2 2 4-4" stroke="#c89a4c" fill="none"/></svg> Personalized Travel Planning</li>
    <li><svg width="8" height="6" viewBox="0 0 8 6"><path d="M1 3l2 2 4-4" stroke="#c89a4c" fill="none"/></svg> Brimwell Vacations &amp; Family Getaways</li>
    <li><svg width="8" height="6" viewBox="0 0 8 6"><path d="M1 3l2 2 4-4" stroke="#c89a4c" fill="none"/></svg> Texas Road Trips &amp; Unique Destinations</li>
    <li><svg width="8" height="6" viewBox="0 0 8 6"><path d="M1 3l2 2 4-4" stroke="#c89a4c" fill="none"/></svg> Stress-Free Travel Support</li>
  </ul>
  <footer class="foot" style="height:34px"><span class="copy">© 2026 Wander Lane Travel. All Right Reserved</span><span class="social"><span></span><span></span></span></footer>
</section>

<!-- ============ CONTACT ============ -->
<section class="page" style="left:82px;top:1104px;width:593px;height:429px">
  <div class="topbar"><span class="tb-item"><i class="tb-ic"><svg width="7" height="5" viewBox="0 0 7 5"><rect x=".3" y=".3" width="6.4" height="4.4" fill="none" stroke="#1f5d69" stroke-width=".6"/><path d="M.3 .3 3.5 2.8 6.7 .3" fill="none" stroke="#1f5d69" stroke-width=".6"/></svg></i>hello@wanderlanetravel.com</span><span class="tb-item"><i class="tb-ic"><svg width="7" height="7" viewBox="0 0 10 10"><path d="M2 1l2 2-1 1.3c.6 1.3 1.5 2.2 2.8 2.8L7 6l2 2-1.2 1.4C4.5 9 1 5.5.6 2.2Z" fill="#1f5d69"/></svg></i>Phone Number (555) 010 2468</span></div>
  <a class="logo" style="left:44px"><span class="logo-dot"></span><span class="logo-name">Wander<br>Lane</span></a>
  <nav class="nav" style="left:156px;top:32px"><svg class="home" viewBox="0 0 10 10"><path d="M5 1 1 5h1.3v4h2.2V6.5h1V9h2.2V5H9Z" fill="#c89a4c"/></svg><a>Brimwell Vacations</a><a>Family Trips</a><a>Texas Road Trips</a><a>Other Destinations</a><a style="margin-left:4px">About Us</a><a class="pill">Contact Us <span class="arrow"><svg width="6" height="6" viewBox="0 0 6 6"><path d="M1 5 5 1M2 1h3v3" stroke="#fff" stroke-width=".8" fill="none"/></svg></span></a></nav>
  <p style="left:58px;top:118px;font-family:'Lexend',sans-serif;font-size:11px;color:var(--teal)">GET IN TOUCH</p>
  <h1 style="left:58px;top:131px;font-family:'Lexend',sans-serif;font-weight:600;font-size:24px;color:var(--teal)">CONTACT US</h1>
  <p style="left:58px;top:168px;width:210px;font-size:7px;line-height:1.85;color:var(--muted)">Let us help you create memorable travel experiences with personalized planning designed around your needs.</p>
  <span style="left:58px;top:212px;width:27px;height:27px;border-radius:50%;background:var(--gold);display:flex;align-items:center;justify-content:center"><svg width="12" height="12" viewBox="0 0 10 10"><path d="M2 1l2 2-1 1.3c.6 1.3 1.5 2.2 2.8 2.8L7 6l2 2-1.2 1.4C4.5 9 1 5.5.6 2.2Z" fill="#fff"/></svg></span>
  <p style="left:95px;top:212px;font-size:8px;line-height:1.55;color:var(--ink)">Phone number<br><span style="font-size:9px">(+555) 010 2468</span></p>
  <span style="left:58px;top:248px;width:190px;height:1px;background:#bcc7c4"></span>
  <span style="left:58px;top:258px;width:27px;height:27px;border-radius:50%;background:var(--gold);display:flex;align-items:center;justify-content:center"><svg width="12" height="9" viewBox="0 0 7 5"><rect x=".3" y=".3" width="6.4" height="4.4" fill="none" stroke="#fff" stroke-width=".6"/><path d="M.3 .3 3.5 2.8 6.7 .3" fill="none" stroke="#fff" stroke-width=".6"/></svg></span>
  <p style="left:96px;top:259px;font-size:8px;line-height:1.55;color:var(--ink)">Email address<br><span style="font-size:8.5px">hello@wanderlanetravel.com</span></p>
  <span style="left:58px;top:310px;width:18px;height:18px;border-radius:50%;background:var(--teal)"></span>
  <span style="left:83px;top:310px;width:18px;height:18px;border-radius:50%;background:var(--teal)"></span>
  <div style="left:298px;top:95px;width:249px;height:257px;background:var(--teal-2);border-radius:4px"></div>
  <p style="left:322px;top:120px;font-family:'Lexend',sans-serif;font-weight:500;font-size:11px;color:var(--white)">START PLANNING YOUR JOURNEY</p>
  <div class="field" style="left:322px;top:148px;width:206px;height:24px;justify-content:flex-start;gap:8px"><svg width="7" height="7" viewBox="0 0 7 7"><circle cx="3.5" cy="2" r="1.5" fill="#8a9597"/><path d="M.6 7c0-2 1.3-3 2.9-3s2.9 1 2.9 3Z" fill="#8a9597"/></svg> Name</div>
  <div class="field" style="left:322px;top:181px;width:206px;height:24px;justify-content:flex-start;gap:8px"><svg width="7" height="5" viewBox="0 0 7 5"><rect x=".3" y=".3" width="6.4" height="4.4" fill="none" stroke="#8a9597" stroke-width=".6"/></svg> Email address</div>
  <div class="field" style="left:322px;top:214px;width:206px;height:24px;justify-content:flex-start;gap:8px"><svg width="6" height="6" viewBox="0 0 10 10"><path d="M2 1l2 2-1 1.3c.6 1.3 1.5 2.2 2.8 2.8L7 6l2 2-1.2 1.4C4.5 9 1 5.5.6 2.2Z" fill="#8a9597"/></svg> Phone number</div>
  <div class="area" style="left:322px;top:246px;width:206px;height:50px;padding:8px 10px">≡&nbsp;&nbsp;Any details you want us to know?</div>
  <div class="btn" style="left:322px;top:306px;width:86px;height:22px;font-size:7.5px;font-weight:500">Contact Us <span class="arrow"><svg width="6" height="6" viewBox="0 0 6 6"><path d="M1 5 5 1M2 1h3v3" stroke="#fff" stroke-width=".8" fill="none"/></svg></span></div>
  <footer class="foot" style="height:34px"><span class="copy">© 2026 Wander Lane Travel. All Right Reserved</span><span class="social"><span></span><span></span></span></footer>
</section>

<!-- ============ BRIMWELL VACATIONS ============ -->
<section class="page" style="left:736px;top:95px;width:600px;height:736px">
  <div class="topbar"><span class="tb-item"><i class="tb-ic"><svg width="7" height="5" viewBox="0 0 7 5"><rect x=".3" y=".3" width="6.4" height="4.4" fill="none" stroke="#1f5d69" stroke-width=".6"/><path d="M.3 .3 3.5 2.8 6.7 .3" fill="none" stroke="#1f5d69" stroke-width=".6"/></svg></i>hello@wanderlanetravel.com</span><span class="tb-item"><i class="tb-ic"><svg width="7" height="7" viewBox="0 0 10 10"><path d="M2 1l2 2-1 1.3c.6 1.3 1.5 2.2 2.8 2.8L7 6l2 2-1.2 1.4C4.5 9 1 5.5.6 2.2Z" fill="#1f5d69"/></svg></i>Phone Number (555) 010 2468</span></div>
  <a class="logo"><span class="logo-dot"></span><span class="logo-name">Wander<br>Lane</span></a>
  <nav class="nav" style="left:156px;top:31px"><svg class="home" viewBox="0 0 10 10"><path d="M5 1 1 5h1.3v4h2.2V6.5h1V9h2.2V5H9Z" fill="#c89a4c"/></svg><a class="active">Brimwell Vacations</a><a>Family Trips</a><a>Texas Road Trips</a><a>Other Destinations</a><a style="margin-left:4px">About Us</a><a class="pill">Contact Us <span class="arrow"><svg width="6" height="6" viewBox="0 0 6 6"><path d="M1 5 5 1M2 1h3v3" stroke="#fff" stroke-width=".8" fill="none"/></svg></span></a></nav>
  <p class="eyebrow" style="top:82px;font-size:10.5px">BRIMWELL VACATIONS</p>
  <h1 class="title" style="top:99px;font-size:21px">EXPLORE BRIMWELL VACATIONS</h1>
  <p class="lead" style="top:132px">Create magical family memories with unforgettable Brimwell vacations — from<br>Brimwell World adventures to magical Brimwell cruises.</p>
  <div class="photo" role="img" aria-label="Costumed characters at a theme park parade" style="left:60px;top:183px;width:121px;height:89px;background:linear-gradient(135deg,#5a3a6a,#c23a3a 50%,#e8c64a)"></div>
  <div class="photo" role="img" aria-label="Cruise ship docked at port" style="left:60px;top:277px;width:121px;height:89px;background:linear-gradient(180deg,#8fb8dc,#f2f2f2 50%,#1f3a5a)"></div>
  <div class="photo" role="img" aria-label="Bronze statue in front of a castle" style="left:186px;top:183px;width:121px;height:183px;background:linear-gradient(180deg,#7fb3e0,#b9d3ea 40%,#8a7a5a 80%,#c8bfa8)"></div>
  <div class="photo" role="img" aria-label="Theme park entrance archway over a road" style="left:312px;top:183px;width:121px;height:89px;background:linear-gradient(180deg,#4f90d8,#3a5fa8 40%,#6a8a5a 75%,#9aa0a0)"></div>
  <div class="photo" role="img" aria-label="Family meeting a character inside a park" style="left:312px;top:277px;width:121px;height:89px;background:linear-gradient(135deg,#6a5a7a,#c99a6a 50%,#4a5a8a)"></div>
  <div class="photo" role="img" aria-label="Pink castle with blue spires" style="left:438px;top:183px;width:121px;height:183px;background:linear-gradient(180deg,#6aa6dc,#c4d8ea 40%,#d9b3b0 65%,#4f7a4a)"></div>
  <div class="tab" style="left:62px;top:404px;width:249px;background:var(--teal);color:var(--white)">BRIMWELL WORLD</div>
  <div class="tab" style="left:313px;top:404px;width:250px;background:var(--beige);color:var(--teal)">BRIMWELL CRUISE</div>
  <div class="panel" style="left:62px;top:432px;width:501px;height:246px;background:var(--white)"></div>
  <span class="lbl" style="left:89px;top:462px">How Many People?</span>
  <span class="lbl" style="left:237px;top:461px">Start Date</span>
  <span class="lbl" style="left:311px;top:462px">End Date</span>
  <span class="lbl" style="left:388px;top:462px">How Many Days at the Parks?</span>
  <div class="field" style="left:88px;top:475px;width:144px;height:25px">Select</div>
  <div class="field" style="left:236px;top:475px;width:70px;height:25px;padding:0 6px"><span class="cal"><svg width="7" height="7" viewBox="0 0 7 7"><rect x=".4" y="1" width="6.2" height="5.6" fill="none" stroke="#8a9597" stroke-width=".6"/></svg>Select Date</span></div>
  <div class="field" style="left:310px;top:475px;width:70px;height:25px;padding:0 6px"><span class="cal"><svg width="7" height="7" viewBox="0 0 7 7"><rect x=".4" y="1" width="6.2" height="5.6" fill="none" stroke="#8a9597" stroke-width=".6"/></svg>Select Date</span></div>
  <div class="field" style="left:387px;top:475px;width:143px;height:25px">Select <svg width="8" height="5" viewBox="0 0 8 5"><path d="M1 1l3 3 3-3" stroke="#333" fill="none"/></svg></div>
  <span class="lbl" style="left:90px;top:508px;font-size:6px">Preferred Resort 1</span>
  <span class="lbl" style="left:238px;top:508px;font-size:6px">Preferred Resort 2</span>
  <div class="field" style="left:88px;top:520px;width:144px;height:25px">Select <svg width="8" height="5" viewBox="0 0 8 5"><path d="M1 1l3 3 3-3" stroke="#333" fill="none"/></svg></div>
  <div class="field" style="left:236px;top:520px;width:144px;height:25px">Select <svg width="8" height="5" viewBox="0 0 8 5"><path d="M1 1l3 3 3-3" stroke="#333" fill="none"/></svg></div>
  <div class="field" style="left:387px;top:520px;width:143px;height:25px">Budget <svg width="8" height="5" viewBox="0 0 8 5"><path d="M1 1l3 3 3-3" stroke="#333" fill="none"/></svg></div>
  <div class="area" style="left:89px;top:560px;width:441px;height:54px;padding:10px">Type here</div>
  <div class="btn" style="left:93px;top:622px;width:121px;font-size:8px">Book Brimwell Trip <span class="arrow"><svg width="6" height="6" viewBox="0 0 6 6"><path d="M1 5 5 1M2 1h3v3" stroke="#fff" stroke-width=".8" fill="none"/></svg></span></div>
  <footer class="foot" style="height:31px"><span class="copy" style="width:100%">© 2026 Wander Lane Travel. All Right Reserved</span><span class="social" style="right:60px"><span></span><span></span></span></footer>
</section>

<!-- ============ FAMILY TRIPS ============ -->
<section class="page" style="left:736px;top:861px;width:595px;height:805px">
  <div class="topbar" style="left:270px"><span class="tb-item"><i class="tb-ic"><svg width="7" height="5" viewBox="0 0 7 5"><rect x=".3" y=".3" width="6.4" height="4.4" fill="none" stroke="#1f5d69" stroke-width=".6"/><path d="M.3 .3 3.5 2.8 6.7 .3" fill="none" stroke="#1f5d69" stroke-width=".6"/></svg></i>hello@wanderlanetravel.com</span><span class="tb-item"><i class="tb-ic"><svg width="7" height="7" viewBox="0 0 10 10"><path d="M2 1l2 2-1 1.3c.6 1.3 1.5 2.2 2.8 2.8L7 6l2 2-1.2 1.4C4.5 9 1 5.5.6 2.2Z" fill="#1f5d69"/></svg></i>Phone Number (555) 010 2468</span></div>
  <a class="logo"><span class="logo-dot"></span><span class="logo-name">Wander<br>Lane</span></a>
  <nav class="nav" style="left:156px;top:31px"><svg class="home" viewBox="0 0 10 10"><path d="M5 1 1 5h1.3v4h2.2V6.5h1V9h2.2V5H9Z" fill="#c89a4c"/></svg><a>Brimwell Vacations</a><a class="active">Family Trips</a><a>Texas Road Trips</a><a>Other Destinations</a><a style="margin-left:4px">About Us</a><a class="pill">Contact Us <span class="arrow"><svg width="6" height="6" viewBox="0 0 6 6"><path d="M1 5 5 1M2 1h3v3" stroke="#fff" stroke-width=".8" fill="none"/></svg></span></a></nav>
  <p class="eyebrow" style="top:80px;font-size:10.5px">OUR FAMILY TRIPS</p>
  <h1 class="title" style="top:96px;font-size:24px">EXPLORE UNIQUE<br>DESTINATIONS</h1>
  <p class="lead" style="top:151px">The best family memories begin with meaningful adventures. Let us help you plan<br>unforgettable trips designed around fun, comfort, and quality time together.</p>
  <div class="photo" role="img" aria-label="Family walking on a pier to overwater villas" style="left:51px;top:210px;width:120px;height:89px;background:linear-gradient(180deg,#8cc0e0,#5aa8c0 55%,#8a7a5a)"></div>
  <div class="photo" role="img" aria-label="Family exploring an old town square" style="left:51px;top:303px;width:120px;height:89px;background:linear-gradient(180deg,#c9d8e4,#b08a6a 45%,#5a4a3a)"></div>
  <div class="photo" role="img" aria-label="Family kayaking in life jackets" style="left:176px;top:210px;width:120px;height:182px;background:linear-gradient(180deg,#7fb6e0,#4a9ab8 35%,#e07a2a 65%,#2a8a9a)"></div>
  <div class="photo" role="img" aria-label="Family playing on a sandy beach" style="left:301px;top:210px;width:120px;height:89px;background:linear-gradient(180deg,#a8cde0,#d8c6a6 55%,#c9ad85)"></div>
  <div class="photo" role="img" aria-label="Family overlooking a coastal town" style="left:301px;top:303px;width:120px;height:89px;background:linear-gradient(180deg,#6aa0d0,#e8e0d4 50%,#8a7a6a)"></div>
  <div class="photo" role="img" aria-label="Family sailing on a boat" style="left:426px;top:210px;width:120px;height:182px;background:linear-gradient(180deg,#d8dde0,#9ab4c4 40%,#3a5a6a 75%,#6a5a4a)"></div>
  <div class="panel" style="left:53px;top:434px;width:496px;height:299px"></div>
  <p class="panel-title" style="top:457px">PLAN YOUR FAMILY TRIP</p>
  <span class="lbl" style="left:81px;top:495px">What Type of Trip Are You Interested In?</span>
  <span class="lbl" style="left:309px;top:495px">How Many People in Your Party?</span>
  <div class="field" style="left:81px;top:511px;width:221px;height:29px">Select <svg width="8" height="5" viewBox="0 0 8 5"><path d="M1 1l3 3 3-3" stroke="#333" fill="none"/></svg></div>
  <div class="field" style="left:307px;top:511px;width:220px;height:29px">Select <svg width="8" height="5" viewBox="0 0 8 5"><path d="M1 1l3 3 3-3" stroke="#333" fill="none"/></svg></div>
  <span class="lbl" style="left:81px;top:553px">What Kind of Trip Are You Looking For?</span>
  <span class="lbl" style="left:311px;top:553px">When Would You Like To Go?</span>
  <div class="field" style="left:81px;top:568px;width:221px;height:29px">Select <svg width="8" height="5" viewBox="0 0 8 5"><path d="M1 1l3 3 3-3" stroke="#333" fill="none"/></svg></div>
  <div class="field" style="left:309px;top:568px;width:107px;height:29px"><span class="cal"><svg width="7" height="7" viewBox="0 0 7 7"><rect x=".4" y="1" width="6.2" height="5.6" fill="none" stroke="#8a9597" stroke-width=".6"/></svg>Start Date</span></div>
  <div class="field" style="left:420px;top:568px;width:107px;height:29px"><span class="cal"><svg width="7" height="7" viewBox="0 0 7 7"><rect x=".4" y="1" width="6.2" height="5.6" fill="none" stroke="#8a9597" stroke-width=".6"/></svg>End Date</span></div>
  <span class="lbl" style="left:81px;top:605px">Any Additional Notes</span>
  <div class="area" style="left:81px;top:620px;width:446px;height:56px">Type here</div>
  <div class="btn" style="left:240px;top:685px;width:125px">Start Planning <span class="arrow"><svg width="6" height="6" viewBox="0 0 6 6"><path d="M1 5 5 1M2 1h3v3" stroke="#fff" stroke-width=".8" fill="none"/></svg></span></div>
  <footer class="foot" style="height:35px"><span class="copy" style="width:100%">© 2026 Wander Lane Travel. All Right Reserved</span><span class="social" style="right:80px"><span></span><span></span></span></footer>
</section>

<!-- ============ OTHER DESTINATIONS ============ -->
<section class="page" style="left:1378px;top:95px;width:599px;height:750px">
  <div class="topbar" style="left:268px"><span class="tb-item"><i class="tb-ic"><svg width="7" height="5" viewBox="0 0 7 5"><rect x=".3" y=".3" width="6.4" height="4.4" fill="none" stroke="#1f5d69" stroke-width=".6"/><path d="M.3 .3 3.5 2.8 6.7 .3" fill="none" stroke="#1f5d69" stroke-width=".6"/></svg></i>hello@wanderlanetravel.com</span><span class="tb-item"><i class="tb-ic"><svg width="7" height="7" viewBox="0 0 10 10"><path d="M2 1l2 2-1 1.3c.6 1.3 1.5 2.2 2.8 2.8L7 6l2 2-1.2 1.4C4.5 9 1 5.5.6 2.2Z" fill="#1f5d69"/></svg></i>Phone Number (555) 010 2468</span></div>
  <a class="logo" style="left:40px"><span class="logo-dot"></span><span class="logo-name">Wander<br>Lane</span></a>
  <nav class="nav" style="left:153px;top:30px"><svg class="home" viewBox="0 0 10 10"><path d="M5 1 1 5h1.3v4h2.2V6.5h1V9h2.2V5H9Z" fill="#c89a4c"/></svg><a>Brimwell Vacations</a><a>Family Trips</a><a>Texas Road Trips</a><a class="active">Other Destinations</a><a style="margin-left:4px">About Us</a><a class="pill">Contact Us <span class="arrow"><svg width="6" height="6" viewBox="0 0 6 6"><path d="M1 5 5 1M2 1h3v3" stroke="#fff" stroke-width=".8" fill="none"/></svg></span></a></nav>
  <p class="eyebrow" style="top:80px;font-size:10.5px">OTHER DESTINATIONS</p>
  <h1 class="title" style="top:97px;font-size:19.5px">EXPLORE UNIQUE DESTINATIONS</h1>
  <p class="lead" style="top:131px">Discover beautiful destinations, hidden gems, scenic escapes, and unforgettable<br>travel experiences tailored to your style.</p>
  <div class="photo" role="img" aria-label="Canal city at sunset" style="left:56px;top:181px;width:121px;height:89px;background:linear-gradient(180deg,#e0a06a,#c88a7a 40%,#6a5a6a 70%,#4a5a6a)"></div>
  <div class="photo" role="img" aria-label="White island village with blue domes" style="left:56px;top:275px;width:121px;height:89px;background:linear-gradient(180deg,#6aa8e0,#f0f0f0 55%,#2a6ab0)"></div>
  <div class="photo" role="img" aria-label="Traveller in a wooden boat between limestone cliffs" style="left:182px;top:181px;width:121px;height:183px;background:linear-gradient(180deg,#4a6a4a,#3a8a8a 45%,#c08a5a 80%,#8a5a3a)"></div>
  <div class="photo" role="img" aria-label="Aerial view of a turquoise coastline" style="left:308px;top:181px;width:121px;height:89px;background:linear-gradient(135deg,#2a8a9a,#9ad8d0 50%,#e8e0c8)"></div>
  <div class="photo" role="img" aria-label="Hikers resting on a mountain trail" style="left:308px;top:275px;width:121px;height:89px;background:linear-gradient(180deg,#c8d8e0,#8a9aa0 45%,#6a7a5a)"></div>
  <div class="photo" role="img" aria-label="Colourful cliffside seaside village" style="left:434px;top:181px;width:120px;height:183px;background:linear-gradient(180deg,#4a90d8,#d8865a 40%,#c9a26b 65%,#2a6f8a)"></div>
  <div class="panel" style="left:54px;top:391px;width:499px;height:301px"></div>
  <p class="panel-title" style="top:413px">PLAN YOUR JOURNEY</p>
  <span class="lbl" style="left:82px;top:453px">What Type of Trip Are You Interested In?</span>
  <span class="lbl" style="left:312px;top:453px">What Kind of Trip Are You Looking For?</span>
  <div class="field" style="left:82px;top:469px;width:221px;height:29px">Select <svg width="8" height="5" viewBox="0 0 8 5"><path d="M1 1l3 3 3-3" stroke="#333" fill="none"/></svg></div>
  <div class="field" style="left:310px;top:468px;width:221px;height:29px">Select <svg width="8" height="5" viewBox="0 0 8 5"><path d="M1 1l3 3 3-3" stroke="#333" fill="none"/></svg></div>
  <span class="lbl" style="left:82px;top:511px">How Many People in Your Party?</span>
  <span class="lbl" style="left:314px;top:511px">When Would You Like To Go?</span>
  <div class="field" style="left:82px;top:527px;width:221px;height:29px">05</div>
  <div class="field" style="left:310px;top:527px;width:108px;height:29px"><span class="cal"><svg width="7" height="7" viewBox="0 0 7 7"><rect x=".4" y="1" width="6.2" height="5.6" fill="none" stroke="#8a9597" stroke-width=".6"/></svg>Start Date</span></div>
  <div class="field" style="left:423px;top:527px;width:108px;height:29px"><span class="cal"><svg width="7" height="7" viewBox="0 0 7 7"><rect x=".4" y="1" width="6.2" height="5.6" fill="none" stroke="#8a9597" stroke-width=".6"/></svg>End Date</span></div>
  <span class="lbl" style="left:82px;top:563px">Any Additional Notes</span>
  <div class="area" style="left:82px;top:578px;width:449px;height:56px">Type here</div>
  <div class="btn" style="left:243px;top:644px;width:125px">Start Planning <span class="arrow"><svg width="6" height="6" viewBox="0 0 6 6"><path d="M1 5 5 1M2 1h3v3" stroke="#fff" stroke-width=".8" fill="none"/></svg></span></div>
  <footer class="foot"><span class="copy" style="width:97%">© 2026 Wander Lane Travel. All Right Reserved</span><span class="social" style="right:82px"><span></span><span></span></span></footer>
</section>

<!-- ============ TEXAS ROAD TRIPS ============ -->
<section class="page" style="left:1378px;top:904px;width:597px;height:719px">
  <div class="topbar" style="left:267px"><span class="tb-item"><i class="tb-ic"><svg width="7" height="5" viewBox="0 0 7 5"><rect x=".3" y=".3" width="6.4" height="4.4" fill="none" stroke="#1f5d69" stroke-width=".6"/><path d="M.3 .3 3.5 2.8 6.7 .3" fill="none" stroke="#1f5d69" stroke-width=".6"/></svg></i>hello@wanderlanetravel.com</span><span class="tb-item"><i class="tb-ic"><svg width="7" height="7" viewBox="0 0 10 10"><path d="M2 1l2 2-1 1.3c.6 1.3 1.5 2.2 2.8 2.8L7 6l2 2-1.2 1.4C4.5 9 1 5.5.6 2.2Z" fill="#1f5d69"/></svg></i>Phone Number (555) 010 2468</span></div>
  <a class="logo" style="left:40px"><span class="logo-dot"></span><span class="logo-name">Wander<br>Lane</span></a>
  <nav class="nav" style="left:153px;top:30px"><svg class="home" viewBox="0 0 10 10"><path d="M5 1 1 5h1.3v4h2.2V6.5h1V9h2.2V5H9Z" fill="#c89a4c"/></svg><a>Brimwell Vacations</a><a>Family Trips</a><a class="active">Texas Road Trips</a><a>Other Destinations</a><a style="margin-left:4px">About Us</a><a class="pill">Contact Us <span class="arrow"><svg width="6" height="6" viewBox="0 0 6 6"><path d="M1 5 5 1M2 1h3v3" stroke="#fff" stroke-width=".8" fill="none"/></svg></span></a></nav>
  <p class="eyebrow" style="top:80px;font-size:10.5px">TEXAS ROAD TRIPS</p>
  <h1 class="title" style="top:96px;font-size:21px">ROAD TRIPS FROM TEXAS</h1>
  <p class="lead" style="top:132px;display:flex;justify-content:center;align-items:center;gap:6px">In Partnership with <span style="width:10px;height:10px;border-radius:50%;background:var(--gold)"></span><b style="font-family:'Lexend',sans-serif;font-weight:500;color:var(--teal)">PINE RIDGE VAN RENTAL</b></p>
  <table class="trips" style="left:56px;top:179px;width:499px">
    <tr><th>Trip Name</th><th>Duration</th><th>Best For</th><th>Destination</th><th>Price Range</th><th>Difficulty</th><th>Van Rental</th></tr>
    <tr><td>TRIP A</td><td>3 Days</td><td>Families</td><td>Big Bend</td><td>$125</td><td>Easy</td><td>Yes</td></tr>
    <tr><td>TRIP B</td><td>5 Days</td><td>Couples</td><td>Hill Country</td><td>$250</td><td>Moderate</td><td>Optional</td></tr>
    <tr><td>TRIP C</td><td>7 Days</td><td>Adventures</td><td>National Parks</td><td>$325</td><td>Moderate</td><td>Yes</td></tr>
    <tr><td>TRIP D</td><td>9 Days</td><td>Adventures</td><td>National Parks</td><td>$450</td><td>Moderate</td><td>Yes</td></tr>
  </table>
  <div class="panel" style="left:55px;top:349px;width:498px;height:301px"></div>
  <p class="panel-title" style="top:373px">PLAN YOUR TEXAS ROAD TRIP</p>
  <span class="lbl" style="left:84px;top:411px">What Type of Trip Are You Interested In?</span>
  <span class="lbl" style="left:312px;top:411px">How Many People in Your Party?</span>
  <div class="field" style="left:84px;top:428px;width:220px;height:28px">Select <svg width="8" height="5" viewBox="0 0 8 5"><path d="M1 1l3 3 3-3" stroke="#333" fill="none"/></svg></div>
  <div class="field" style="left:311px;top:427px;width:220px;height:28px">05 <svg width="8" height="5" viewBox="0 0 8 5"><path d="M1 1l3 3 3-3" stroke="#333" fill="none"/></svg></div>
  <span class="lbl" style="left:84px;top:469px">Do You Need a Van Rental</span>
  <span class="lbl" style="left:315px;top:469px">When Would You Like To Go?</span>
  <div class="field" style="left:84px;top:485px;width:220px;height:28px">Pine Ridge Van Rentals - Cedar Hollow, TX</div>
  <div class="field" style="left:311px;top:485px;width:108px;height:28px"><span class="cal"><svg width="7" height="7" viewBox="0 0 7 7"><rect x=".4" y="1" width="6.2" height="5.6" fill="none" stroke="#8a9597" stroke-width=".6"/></svg>Start Date</span></div>
  <div class="field" style="left:423px;top:485px;width:108px;height:28px"><span class="cal"><svg width="7" height="7" viewBox="0 0 7 7"><rect x=".4" y="1" width="6.2" height="5.6" fill="none" stroke="#8a9597" stroke-width=".6"/></svg>End Date</span></div>
  <span class="lbl" style="left:84px;top:521px">Any Additional Notes</span>
  <div class="area" style="left:84px;top:536px;width:447px;height:56px">Type here</div>
  <div class="btn" style="left:244px;top:601px;width:125px">Start Planning <span class="arrow"><svg width="6" height="6" viewBox="0 0 6 6"><path d="M1 5 5 1M2 1h3v3" stroke="#fff" stroke-width=".8" fill="none"/></svg></span></div>
  <footer class="foot" style="height:34px"><span class="copy" style="width:98%">© 2026 Wander Lane Travel. All Right Reserved</span><span class="social" style="right:80px"><span></span><span></span></span></footer>
</section>

</main>
</body>
</html>
```